Meridale Bed Company Needs Business Card

Looking for a very nice looking business card. Creative but not extravagant. We sell beds and pillows across the U.S. and need something professional but catchy. I have attached the logo.

Name : Devin Holt
Title : President
Phone : (800) 471-2960
Email: sleep@quilmora.com
Website: www.quilmora.com

Can be single-sided or double-sided
horizontal or vertical

Can use Blues/Greys

Target Market(s)

Mass Market

Industry/Entity Type

Retail

Contact Information for Business Card

Name : Devin Holt
Title : President
Phone : (800) 471-2960
Email: sleep@quilmora.com
Website: www.quilmora.com

Requirements
Must have
• Clean, Modern, Smooth
• Can use Blues/Greys
• On the other side without the information - have something simple like www.quilmora.com or our logo
Nice to have
• Surprise me
Should not have
• Nothing crazy, nothing cluttered

```html
<!DOCTYPE html>
<html lang="en">
<head>
<meta charset="utf-8">
<title>Meridale Bed Company – Business Card</title>
<link rel="stylesheet" href="https://fonts.googleapis.com/css2?family=Arimo:wght@400&display=swap">
<style>
  :root {
    --page: #eceef0;
    --card: #ffffff;
    --brand-blue: #34b3d8;
    --deep-blue: #1f8fb8;
    --pale-blue: #d8eef7;
    --frame-grey: #e6e8ea;
    --text-grey: #4a4d50;
    --muted-grey: #8a8d90;
  }
  * { margin: 0; padding: 0; box-sizing: border-box; }
  html, body { width: 1200px; height: 1023px; overflow: hidden; background: var(--page); }
  .sheet { position: relative; width: 1200px; height: 1023px; }
  .card {
    position: absolute; left: 250px; width: 700px; height: 400px;
    background: var(--card); border-radius: 22px; overflow: hidden;
    box-shadow: 0 10px 30px rgba(0,0,0,.12);
  }
  .card--front { top: 90px; }
  .card--back { top: 533px; }
  .card__shapes { position: absolute; inset: 0; width: 100%; height: 100%; }

  .wordmark {
    position: absolute; font-family: "Arimo", sans-serif; font-weight: 400;
    color: var(--brand-blue); line-height: 1; white-space: nowrap;
  }
  .card--front .wordmark { left: 90px; bottom: 86px; font-size: 72px; }
  .card--back .wordmark { left: 0; right: 0; top: 156px; text-align: center; font-size: 88px; }

  .holder { position: absolute; right: 48px; top: 40px; text-align: right; font-family: "Arimo", sans-serif; }
  .holder__name { font-size: 24px; color: var(--brand-blue); }
  .holder__title { font-size: 15px; color: var(--muted-grey); margin-top: 3px; }

  .contact { position: absolute; right: 40px; top: 150px; list-style: none; font-family: "Arimo", sans-serif; font-size: 15px; color: var(--text-grey); }
  .contact__item { display: flex; align-items: center; justify-content: flex-end; gap: 12px; height: 30px; }
  .contact__icon { width: 18px; height: 18px; }
</style>
</head>
<body>
<main class="sheet">

  <section class="card card--front" aria-label="Card front">
    <svg class="card__shapes" viewBox="0 0 700 400" aria-hidden="true">
      <rect x="40" y="150" width="430" height="430" transform="rotate(-14 255 365)" fill="var(--frame-grey)" opacity=".7"/>
      <rect x="20" y="200" width="380" height="380" transform="rotate(-14 210 390)" fill="var(--pale-blue)"/>
      <rect x="52" y="232" width="316" height="316" transform="rotate(-14 210 390)" fill="var(--card)"/>
    </svg>
    <div class="holder">
      <p class="holder__name">Devin Holt</p>
      <p class="holder__title">President</p>
    </div>
    <ul class="contact">
      <li class="contact__item">(800) 471-2960
        <svg class="contact__icon" viewBox="0 0 18 18"><rect x="4" y="1.5" width="10" height="15" rx="2" fill="none" stroke="var(--brand-blue)" stroke-width="1.4"/><circle cx="9" cy="13.5" r="1" fill="var(--brand-blue)"/></svg>
      </li>
      <li class="contact__item">sleep@quilmora.com
        <svg class="contact__icon" viewBox="0 0 18 18"><rect x="1.5" y="4" width="15" height="10" rx="1" fill="none" stroke="var(--brand-blue)" stroke-width="1.4"/><path d="M2 5l7 5 7-5" fill="none" stroke="var(--brand-blue)" stroke-width="1.4"/></svg>
      </li>
      <li class="contact__item">www.quilmora.com
        <svg class="contact__icon" viewBox="0 0 18 18"><circle cx="9" cy="9" r="7.5" fill="none" stroke="var(--brand-blue)" stroke-width="1.4"/><ellipse cx="9" cy="9" rx="3.2" ry="7.5" fill="none" stroke="var(--brand-blue)" stroke-width="1.2"/><path d="M1.5 9h15" stroke="var(--brand-blue)" stroke-width="1.2"/></svg>
      </li>
    </ul>
    <p class="wordmark">quilmora</p>
  </section>

  <section class="card card--back" aria-label="Card back">
    <svg class="card__shapes" viewBox="0 0 700 400" aria-hidden="true">
      <defs>
        <linearGradient id="side-blue" x1="0" y1="0" x2="0" y2="1">
          <stop offset="0" stop-color="var(--brand-blue)"/>
          <stop offset="1" stop-color="var(--deep-blue)"/>
        </linearGradient>
      </defs>
      <circle cx="-330" cy="200" r="420" fill="url(#side-blue)"/>
      <circle cx="-330" cy="200" r="432" fill="none" stroke="var(--brand-blue)" stroke-width="2.5"/>
      <circle cx="1030" cy="200" r="420" fill="url(#side-blue)"/>
      <circle cx="1030" cy="200" r="432" fill="none" stroke="var(--brand-blue)" stroke-width="2.5"/>
    </svg>
    <p class="wordmark">quilmora</p>
  </section>

</main>
</body>
</html>
```